Cafe Business needs a business card design

I already have an ai logo I would like to use and color. I need someone to make a business card for me on adobe illustrator with it. Its for a cafe restaurant opening in Japan I would like to be able to change out the names, contact info, ect on my own from adobe illustrator.

Industry/Entity Type

Business

Contact Information for Business Card

Double sided with logo on one side and info on the other. Name, Tel, fax, email and west

```html
<!DOCTYPE html>
<html lang="en">
<head>
<meta charset="utf-8">
<title>Oaken Cup Cafe – Business Card</title>
<link rel="stylesheet" href="https://fonts.googleapis.com/css2?family=Open+Sans:wght@400;600;800&display=swap">
<style>
  :root {
    --coffee: #4a2e1f;
    --coffee-deep: #3a2216;
    --cream: #efe6d6;
    --paper: #ffffff;
    --backdrop: #e9e6e2;
    --ink: #3b2518;
  }
  * { margin: 0; padding: 0; box-sizing: border-box; }
  html, body { width: 1200px; height: 913px; overflow: hidden; }
  body {
    background: var(--backdrop);
    font-family: "Open Sans", Arial, sans-serif;
    position: relative;
  }
  .card {
    position: absolute;
    top: 301px;
    width: 540px;
    height: 310px;
    border-radius: 18px;
    background: var(--paper);
    overflow: hidden;
    box-shadow: 0 6px 18px rgba(0,0,0,0.15);
  }
  .card--front { left: 40px; }
  .card--back  { left: 620px; }
  .card__shape { position: absolute; inset: 0; }

  .brand {
    position: absolute;
    display: flex;
    align-items: center;
    gap: 14px;
  }
  .brand__square {
    width: 54px;
    height: 54px;
    background: var(--coffee);
    flex: none;
  }
  .brand__name {
    color: var(--ink);
    font-weight: 800;
    font-size: 24px;
    line-height: 1.05;
    letter-spacing: 0.5px;
    text-transform: uppercase;
  }
  .card--front .brand { left: 40px; top: 118px; }
  .card--back .brand { left: 50%; top: 50%; transform: translate(-50%, -50%); }
  .card--back .brand__square { width: 64px; height: 64px; }
  .card--back .brand__name { font-size: 28px; }

  .contact {
    position: absolute;
    right: 26px;
    top: 84px;
    text-align: right;
    color: var(--cream);
  }
  .contact__name {
    font-size: 18px;
    font-weight: 600;
    letter-spacing: 0.5px;
    text-transform: uppercase;
  }
  .contact__role {
    font-size: 9px;
    letter-spacing: 1px;
    text-transform: uppercase;
    margin-bottom: 8px;
    opacity: 0.85;
  }
  .contact__line {
    display: flex;
    justify-content: flex-end;
    align-items: center;
    gap: 6px;
    font-size: 11px;
    line-height: 17px;
  }
  .contact__icon { width: 10px; height: 10px; flex: none; }
</style>
</head>
<body>

<section class="card card--front" aria-label="Business card, contact side">
  <svg class="card__shape" viewBox="0 0 540 310" aria-hidden="true">
    <path fill="var(--coffee)" d="M540,55 H282 Q255,55 255,82 V205 Q255,242 222,250 Q200,256 200,280 V310 H540 Z"/>
    <rect x="505" y="55" width="35" height="24" fill="var(--cream)"/>
  </svg>

  <div class="brand">
    <span class="brand__square"></span>
    <span class="brand__name">Oaken Cup<br>Cafe</span>
  </div>

  <div class="contact">
    <p class="contact__name">Kenji Arata</p>
    <p class="contact__role">Owner</p>
    <p class="contact__line">+81 3555-0142
      <svg class="contact__icon" viewBox="0 0 10 10"><path fill="currentColor" d="M2 0.5 L4 2.5 L3 3.8 Q4 6 6.2 7 L7.5 6 L9.5 8 L8 9.5 Q2.5 9 0.5 2 Z"/></svg>
    </p>
    <p class="contact__line">+81 3555-0187
      <svg class="contact__icon" viewBox="0 0 10 10"><rect x="1" y="3" width="8" height="6" fill="currentColor"/><rect x="2.5" y="0.5" width="5" height="3" fill="none" stroke="currentColor"/></svg>
    </p>
    <p class="contact__line">kenji@oakencupcafe.com
      <svg class="contact__icon" viewBox="0 0 10 10"><rect x="0.5" y="2" width="9" height="6.5" fill="none" stroke="currentColor"/><path d="M0.5 2 L5 6 L9.5 2" fill="none" stroke="currentColor"/></svg>
    </p>
    <p class="contact__line">www.oakencupcafe.com
      <svg class="contact__icon" viewBox="0 0 10 10"><circle cx="5" cy="5" r="4.3" fill="none" stroke="currentColor"/><path d="M0.7 5 H9.3 M5 0.7 Q2 5 5 9.3 M5 0.7 Q8 5 5 9.3" fill="none" stroke="currentColor" stroke-width="0.8"/></svg>
    </p>
  </div>
</section>

<section class="card card--back" aria-label="Business card, brand side">
  <div class="brand">
    <span class="brand__square"></span>
    <span class="brand__name">Oaken Cup<br>Cafe</span>
  </div>
</section>

</body>
</html>
```